Birchline Septic Solutions

Would like to see some single sided ones but would also like to see some double sided with one sided only being the logo. Owners name is Colin Vandro. Phone number is 555-214-0387
Services are pumping, inspections, installs, and repairs

Contact Information for Business Card

555-241-0387 Colin Vandro Maplewood, OH

```html
<!DOCTYPE html>
<html lang="en">
<head>
<meta charset="utf-8">
<title>Birchline Septic Solutions – Business Cards</title>
<link href="https://fonts.googleapis.com/css2?family=Montserrat:wght@400;700;800&display=swap" rel="stylesheet">
<style>
  :root {
    --backdrop: #4a4a49;
    --card: #161616;
    --teal: #2dbdb6;
    --white: #ffffff;
    --emboss: #222222;
  }
  * { margin: 0; padding: 0; box-sizing: border-box; }
  html, body { width: 1200px; height: 801px; overflow: hidden; }
  body {
    background: var(--backdrop);
    font-family: "Montserrat", sans-serif;
    display: flex;
    align-items: center;
    justify-content: center;
    gap: 40px;
  }
  .card {
    position: relative;
    width: 540px;
    height: 309px;
    background: var(--card);
    border-bottom: 3px solid var(--teal);
    border-left: 2px solid var(--teal);
    overflow: hidden;
  }

  /* Front */
  .card-front { display: flex; align-items: center; }
  .brand-block {
    width: 285px;
    height: 100%;
    display: flex;
    align-items: center;
    justify-content: center;
    gap: 12px;
    padding: 0 24px;
  }
  .brand-mark {
    width: 16px; height: 16px;
    background: var(--teal);
    flex: none;
  }
  .brand-name {
    color: var(--white);
    font-weight: 800;
    font-size: 24px;
    line-height: 1.15;
    text-transform: uppercase;
    letter-spacing: 0.5px;
  }
  .divider {
    width: 1.5px;
    height: 150px;
    background: var(--teal);
    flex: none;
  }
  .contact-block { padding-left: 28px; color: var(--white); }
  .owner-name {
    color: var(--teal);
    font-weight: 700;
    font-size: 22px;
    line-height: 1.1;
    white-space: nowrap;
  }
  .owner-town { font-size: 12px; margin-bottom: 18px; }
  .contact-list { list-style: none; font-size: 12px; line-height: 1.55; }
  .contact-list li { display: flex; align-items: center; gap: 8px; white-space: nowrap; }
  .contact-list svg { width: 10px; height: 10px; flex: none; }
  .address { font-size: 12px; line-height: 1.4; margin-top: 14px; padding-left: 18px; }

  /* Back */
  .card-back { display: flex; flex-direction: column; }
  .back-brand {
    flex: 1;
    display: flex;
    align-items: center;
    justify-content: center;
    gap: 16px;
    padding-top: 10px;
  }
  .back-brand .brand-mark { width: 22px; height: 22px; background: var(--emboss); }
  .back-brand .brand-name {
    color: var(--emboss);
    font-size: 34px;
    text-align: left;
  }
  .services-band {
    background: var(--teal);
    color: var(--white);
    font-size: 15px;
    padding: 6px 0;
    text-align: center;
    margin-bottom: 36px;
  }
</style>
</head>
<body>
  <section class="card card-front">
    <div class="brand-block">
      <span class="brand-mark"></span>
      <span class="brand-name">Birchline<br>Septic Solutions</span>
    </div>
    <div class="divider"></div>
    <div class="contact-block">
      <h1 class="owner-name">Colin Vandro</h1>
      <p class="owner-town">Maplewood</p>
      <ul class="contact-list">
        <li>
          <svg viewBox="0 0 10 10" aria-hidden="true"><path d="M2 0.5 L4 2.6 L3 3.8 Q4.2 6 6.2 7 L7.4 6 L9.5 8 L8.2 9.5 Q2.5 8.5 0.5 1.8 Z" fill="var(--teal)"/></svg>
          555-214-0387
        </li>
        <li>
          <svg viewBox="0 0 10 10" aria-hidden="true"><rect x="0.5" y="2" width="9" height="6.5" fill="var(--teal)"/><path d="M0.5 2 L5 5.5 L9.5 2" stroke="var(--card)" fill="none" stroke-width="0.9"/></svg>
          info@birchlineseptic.com
        </li>
        <li>
          <svg viewBox="0 0 10 10" aria-hidden="true"><circle cx="5" cy="5" r="4.5" fill="var(--teal)"/><path d="M0.5 5 H9.5 M5 0.5 V9.5" stroke="var(--card)" stroke-width="0.7"/></svg>
          www.birchlineseptic.com
        </li>
      </ul>
      <p class="address">Your address, City<br>State, Zip 1234</p>
    </div>
  </section>

  <section class="card card-back">
    <div class="back-brand">
      <span class="brand-mark"></span>
      <span class="brand-name">Birchline<br>Septic Solutions</span>
    </div>
    <p class="services-band">Services are pumping, inspections, installs, and repairs</p>
  </section>
</body>
</html>
```